Small Business Broker Business Card Design

A business card design for a small business brokerage, which is a financial service, not unlike real estate brokerage, but for small businesses such as laundromats, pizza shops, restaurants, cleaners etc. The designs should all be simple, more conservative in nature, using the colors and font of the logo. Again, think real estate Brokerage as a business context
Contact Information for Business Card
Name: Glen R. Harlow. Title: Small Business Advisor. Email: g.harlow@bayfieldcapitalworks.example. Mobile: (555) 274-3918. Office: (555) 806-2147. www.bayfieldcapitalworks.example

```html
<!DOCTYPE html>
<html lang="en">
<head>
<meta charset="utf-8">
<title>Bayfield Capital Works – Business Card</title>
<link href="https://fonts.googleapis.com/css2?family=Montserrat:wght@400;500;600;700&display=swap" rel="stylesheet">
<style>
  :root {
    --navy: #1e3a6e;
    --green: #8cc63f;
    --green-light: #b9dd82;
    --ink: #1f2a3d;
    --white: #ffffff;
    --backdrop: #9a9a9a;
  }
  * { box-sizing: border-box; margin: 0; padding: 0; }
  html, body {
    width: 1093px; height: 1200px; overflow: hidden;
    background: var(--backdrop);
    font-family: "Montserrat", sans-serif;
  }
  .canvas { position: relative; width: 1093px; height: 1200px; }
  .card {
    position: absolute; left: 264px; width: 581px; height: 363px;
    border-radius: 20px; overflow: hidden;
  }
  .card--front { top: 225px; background: var(--white); }
  .card--back { top: 614px; background: var(--green); }

  /* front */
  .brand {
    position: absolute; left: 20px; width: 244px; top: 178px;
    display: flex; flex-direction: column; align-items: center;
  }
  .brand__name {
    display: flex; align-items: center; gap: 6px;
    color: var(--navy); font-weight: 700; font-size: 12.5px; line-height: 15px;
    letter-spacing: 0.2px; white-space: nowrap;
  }
  .brand__square { width: 9px; height: 9px; background: var(--green); }
  .brand__tagline {
    margin-top: 2px; color: var(--green); font-weight: 600; font-size: 6.3px;
    letter-spacing: 0.9px; text-transform: uppercase; white-space: nowrap;
  }
  .divider {
    position: absolute; left: 272px; top: 89px; width: 1.5px; height: 148px; background: var(--navy);
  }
  .person { position: absolute; left: 283px; top: 88px; }
  .person__name { color: var(--navy); font-weight: 700; font-size: 21.5px; line-height: 1.1; }
  .person__title { color: var(--ink); font-weight: 500; font-size: 12.5px; margin-top: 2px; }
  .contact { position: absolute; left: 286px; top: 160px; list-style: none; }
  .contact__item {
    display: flex; align-items: center; gap: 9px;
    color: var(--ink); font-size: 12.8px; font-weight: 500; height: 19.5px;
  }
  .contact__item:nth-child(2) { margin-top: 4px; }
  .contact__icon { width: 11px; height: 11px; fill: var(--navy); flex: none; }
  .swoosh { position: absolute; left: 0; top: 0; width: 581px; height: 363px; }

  /* back */
  .texture {
    position: absolute; inset: 0;
    background: radial-gradient(ellipse 60% 70% at 95% 5%, rgba(230,242,200,0.55), rgba(230,242,200,0) 70%),
                var(--green);
  }
  .back-brand {
    position: absolute; left: 0; right: 0; top: 215px;
    display: flex; flex-direction: column; align-items: center;
  }
  .back-brand__square { width: 30px; height: 30px; background: var(--navy); margin-bottom: 26px; }
  .back-brand__name { color: var(--navy); font-weight: 700; font-size: 20.5px; letter-spacing: 0.3px; white-space: nowrap; }
  .back-brand__tagline {
    margin-top: 4px; color: var(--white); font-weight: 600; font-size: 10.2px;
    letter-spacing: 1.6px; text-transform: uppercase; white-space: nowrap;
  }
</style>
</head>
<body>
<main class="canvas">

  <section class="card card--front">
    <div class="brand">
      <div class="brand__name"><span class="brand__square"></span>BAYFIELD CAPITAL WORKS, INC</div>
      <div class="brand__tagline">Trusted guidance to buy or sell your business</div>
    </div>

    <div class="divider"></div>

    <div class="person">
      <h1 class="person__name">Glen R. Harlow</h1>
      <p class="person__title">Small Business Advisor</p>
    </div>

    <ul class="contact">
      <li class="contact__item">
        <svg class="contact__icon" viewBox="0 0 12 12"><path d="M1 4.5C1 2.5 3 1.5 6 1.5s5 1 5 3H8.5V3.5h-5v1H1z"/><rect x="2" y="5.5" width="8" height="5" rx="1"/></svg>
        (555) 806-2147
      </li>
      <li class="contact__item">
        <svg class="contact__icon" viewBox="0 0 12 12"><path d="M2.5 1l2 2.5-1 1.2c.6 1.3 1.5 2.2 2.8 2.8l1.2-1 2.5 2-1.2 1.8C5.3 10 2 6.7 1.2 2.2z"/></svg>
        (555) 274-3918
      </li>
      <li class="contact__item">
        <svg class="contact__icon" viewBox="0 0 12 12"><path d="M1 3h10v.8L6 6.6 1 3.8z"/><path d="M1 4.9l5 2.8 5-2.8V9H1z"/></svg>
        g.harlow@bayfieldcapitalworks.example
      </li>
      <li class="contact__item">
        <svg class="contact__icon" viewBox="0 0 12 12"><circle cx="6" cy="6" r="5"/><path d="M3.5 3.5l2 1-.5 2 1.5 1.5-.5 2" stroke="#fff" stroke-width="1" fill="none"/></svg>
        www.bayfieldcapitalworks.example
      </li>
    </ul>

    <svg class="swoosh" viewBox="0 0 581 363" aria-hidden="true">
      <path d="M0 363 L8 358 Q301 262 572 356 L581 363 Z" fill="var(--green)"/>
      <path d="M3 353 Q301 250 577 351" fill="none" stroke="var(--navy)" stroke-width="3.2"/>
    </svg>
  </section>

  <section class="card card--back">
    <div class="texture" role="img" aria-label="Repeating pattern of faint light-green brand marks across the card"></div>
    <div class="back-brand">
      <span class="back-brand__square"></span>
      <div class="back-brand__name">BAYFIELD CAPITAL WORKS, INC</div>
      <div class="back-brand__tagline">Trusted guidance to buy or sell your business</div>
    </div>
  </section>

</main>
</body>
</html>
```